Animal Eye Clinic needs a Business card

We are a new veterinary ophthalmology practice (Ridgeline Pet Vision Care) and we need a business card designed. We only see animal eyes - we are not a regular veterinary clinic. We already have a logo. We are looking for a professional, good looking business card to hand out to our clients. We are looking for something simple but professional and contemporary. Our logo is likely the only picture/graphic that needs to be on the card.
Updates

Contact Information for Business Card

Delia Vossman, BSc, DVM, MSc, DipACVO
Veterinary Ophthalmologist

Phone: 250.418.3927
Email: ridgelinepetvisioncare@mailbox-example.net
Website: ridgelinepetvisioncare-example.net
Address: 1874 Thornbury Rd
Kelowna, BC, V1X 4M9

Colors

Designer to choose colors to be used in the design.

Requirements
Must have
• Our logo (attached)

```html
<!DOCTYPE html>
<html lang="en">
<head>
<meta charset="utf-8">
<title>Ridgeline Pet Vision Care — Business Card</title>
<link rel="stylesheet" href="https://fonts.googleapis.com/css2?family=Open+Sans:wght@400;600;700&display=swap">
<style>
  :root {
    --teal: #0a97a9;
    --teal-deep: #0b8d9e;
    --ink: #4a4a4a;
    --rule: #9a9a9a;
    --paper: #ffffff;
    --backdrop: #e4e4e4;
  }
  * { box-sizing: border-box; margin: 0; padding: 0; }
  html, body { width: 1200px; height: 800px; overflow: hidden; }
  body {
    background: var(--backdrop);
    font-family: "Open Sans", sans-serif;
    position: relative;
  }
  .card {
    position: absolute;
    width: 540px;
    height: 308px;
    box-shadow: 0 8px 24px rgba(0,0,0,0.18);
  }
  /* Front */
  .card--front { left: 70px; top: 90px; background: var(--paper); }
  .brand {
    position: absolute; top: 34px; right: 34px;
    display: flex; align-items: center; gap: 10px;
  }
  .brand__dot { width: 26px; height: 26px; border-radius: 50%; background: var(--teal); }
  .brand__name { color: var(--teal); font-weight: 700; font-size: 18px; letter-spacing: 0.2px; }
  .person { position: absolute; left: 34px; top: 158px; }
  .person__name { color: var(--teal); font-weight: 700; font-size: 17px; }
  .person__creds { color: var(--teal); font-weight: 400; font-size: 11px; }
  .person__title { color: var(--ink); font-size: 13px; margin-top: 1px; }
  .divider {
    position: absolute; left: 34px; right: 34px; top: 210px;
    height: 1px; background: var(--rule);
  }
  .contacts { position: absolute; left: 34px; top: 222px; list-style: none; }
  .contacts li {
    display: flex; align-items: center; gap: 7px;
    color: var(--ink); font-size: 11.5px; line-height: 19px;
  }
  .contacts svg { width: 12px; height: 12px; flex: none; }
  .address {
    position: absolute; right: 34px; top: 222px;
    text-align: right; color: var(--ink); font-size: 11.5px; line-height: 19px;
    font-style: normal;
  }
  /* Back */
  .card--back { left: 590px; top: 402px; background: var(--teal); }
  .back-brand {
    position: absolute; left: 0; right: 0; top: 112px;
    display: flex; justify-content: center; align-items: center; gap: 14px;
  }
  .back-brand__dot { width: 40px; height: 40px; border-radius: 50%; background: var(--paper); }
  .back-brand__name { color: var(--paper); font-weight: 700; font-size: 24px; }
  .back-url {
    position: absolute; left: 0; right: 0; bottom: 30px;
    text-align: center; color: var(--paper); font-size: 12px; letter-spacing: 3px;
  }
</style>
</head>
<body>
  <section class="card card--front" aria-label="Business card front">
    <div class="brand">
      <span class="brand__dot"></span>
      <span class="brand__name">Ridgeline Pet Vision Care</span>
    </div>

    <div class="person">
      <p class="person__name">Delia Vossman, <span class="person__creds">BSc, DVM, MSc, DipACVO</span></p>
      <p class="person__title">Veterinary Ophthalmologist</p>
    </div>

    <div class="divider"></div>

    <ul class="contacts">
      <li>
        <svg viewBox="0 0 12 12" aria-hidden="true"><path fill="var(--teal)" d="M2.5 1h2l1 2.6-1.3 1a6 6 0 0 0 3.2 3.2l1-1.3 2.6 1v2a1 1 0 0 1-1 1A9.5 9.5 0 0 1 1.5 2a1 1 0 0 1 1-1z"/></svg>
        250.418.3927
      </li>
      <li>
        <svg viewBox="0 0 12 12" aria-hidden="true"><rect x="0.5" y="2.5" width="11" height="7" rx="1" fill="var(--teal)"/><path d="M1 3l5 3.5L11 3" stroke="#fff" stroke-width="1" fill="none"/></svg>
        ridgelinepetvisioncare@mailbox-example.net
      </li>
      <li>
        <svg viewBox="0 0 12 12" aria-hidden="true"><circle cx="6" cy="6" r="5.5" fill="var(--teal)"/><path d="M0.8 6h10.4M6 0.8c-2.2 2.8-2.2 7.6 0 10.4M6 0.8c2.2 2.8 2.2 7.6 0 10.4" stroke="#fff" stroke-width="0.8" fill="none"/></svg>
        ridgelinepetvisioncare-example.net
      </li>
    </ul>

    <address class="address">
      1874 Thornbury Rd<br>
      Kelowna, BC, V1X 4M9
    </address>
  </section>

  <section class="card card--back" aria-label="Business card back">
    <div class="back-brand">
      <span class="back-brand__dot"></span>
      <span class="back-brand__name">Ridgeline Pet Vision Care</span>
    </div>
    <p class="back-url">www.ridgelinepetvisioncare-example.net</p>
  </section>
</body>
</html>
```